Eyecatching website design for commercial lighting business

This contest is all about the graphic design aspect. We need a striking website design for a commercial lighting company. We want something really eye catching to introduce people to our range of induction and LED lights which save businesses money on maintenance and electricity costs.

To be successful in this contest you will need to provide a design and pictures for the pages listed below.

We are using the platform velbrin.com.au and you can see the attached template which everything will be loaded into so we just need HTML files which we can upload and we can do everything else from Velbrin.

The final design should be strong and clean and use the colours and textures in the attached business card file.

Detailed requirements:

Please see attached screenshot of the website template, all we need is a fantastic graphic design and improvement/ incorporation of our logo for the following pages
Page Headings:
1. Home
About Us, Contact Us, snapshot of and link to Blog

Each of the below pages will have several paragraphs of text followed by a list of suitable products which is generated from our product catalogue.

2. Car Park Lighting
3. Educational Lighting
4. Hospitality Lighting
5. Office & Shop Lighting
6. Warehouse Lighting

Some of the website we have seen which are similar in nature are:
http://www.quorvanlamps.com.au/
http://www.tibrox.com/
http://www.gandowlumen.net/commercial-led
but we really want a modern, eye catching and memorable design

Some of the designs built on Velbrin that we like are:

http://www.pemberhollow.com.au/
http://www.marwickgoods.com.au/
http://www.kelmorabay.com.au/

I've also uploaded a couple of photos that we love. We'd like something similar for each industry.

Target Market(s)

Company Owners, Maintenance & Facilities Managers, Electrical Contractors

Industry/Entity Type

Electrical

Coding

Coded - Design and coding required

Number of Pages Required

5+ page

Font styles to use
Sans Serif

Colors
33a6d7
ec1f27

Requirements
Must have
• -Must scale to mobile
• -HTML coded files need to be provided (HTML Bootstrap)
Nice to have
• -Prefer incorporation of our logo into header bar
• -Design of 2-3 advertising banners which can be displayed on the home page
• -Prominent call to action button towards top of page 'Get a quote' or similar
• -Grid based design HTML Bootstrap

```html
<!DOCTYPE html>
<html lang="en">
<head>
<meta charset="utf-8">
<title>Harlow &amp; Venn Business Solutions – Commercial Lighting</title>
<link href="https://fonts.googleapis.com/css2?family=Oswald:wght@400;500;600&family=Open+Sans:wght@400;600;700&display=swap" rel="stylesheet">
<style>
:root{
  --blue:#33a6d7;
  --red:#ec1f27;
  --ink:#2d2d2d;
  --muted:#777;
  --light:#f1f2f3;
  --dark:#1e2124;
  --darker:#15171a;
  --white:#fff;
}
*{box-sizing:border-box;margin:0;padding:0}
html,body{width:1200px;height:2784px;overflow:hidden}
body{font-family:"Open Sans",Arial,sans-serif;color:var(--ink);background:var(--white);position:relative}
.heading{font-family:"Oswald",Arial,sans-serif;text-transform:uppercase;font-weight:500}
p{font-size:14px;line-height:1.65;color:var(--muted)}
.btn{display:inline-block;font-family:"Oswald",Arial,sans-serif;text-transform:uppercase;font-size:15px;color:var(--white);padding:12px 26px;border-radius:3px}
.btn-blue{background:var(--blue)}
.btn-red{background:var(--red)}

/* header + hero */
.hero{position:absolute;left:0;top:0;width:1200px;height:730px;background:linear-gradient(160deg,#3d4650 0%,#1f2833 45%,#0e1319 100%)}
.hero-photo{position:absolute;inset:0;background:radial-gradient(ellipse at 70% 55%,rgba(240,190,110,.45),transparent 55%),radial-gradient(ellipse at 20% 85%,rgba(60,90,60,.6),transparent 50%)}
.topbar{position:absolute;left:0;top:0;width:1200px;height:84px;background:rgba(10,12,15,.78);display:flex;align-items:center;justify-content:space-between;padding:0 0 0 60px}
.brand{display:flex;align-items:center;gap:12px;font-family:"Oswald",Arial,sans-serif;font-size:24px;font-weight:500;color:var(--white);text-transform:uppercase}
.brand-mark{width:34px;height:34px;background:var(--red)}
.nav{display:flex;height:84px}
.nav a{display:flex;align-items:center;padding:0 26px;font-family:"Oswald",Arial,sans-serif;font-size:15px;color:var(--white);text-transform:uppercase;background:var(--red);border-left:1px solid rgba(255,255,255,.25)}
.nav a.active{background:#c8141b}
.hero-copy{position:absolute;left:112px;top:240px;width:560px}
.hero-copy h1{font-size:84px;color:var(--blue);line-height:1;font-weight:600}
.hero-copy h2{font-size:30px;color:var(--white);margin:14px 0 18px;font-weight:400}
.hero-copy p{color:#e4e4e4;font-size:18px;line-height:1.55;margin-bottom:34px}
.hero-copy .btn{font-size:18px;padding:14px 30px}
.arrow{position:absolute;width:46px;height:46px;border-radius:50%;background:rgba(255,255,255,.25);display:flex;align-items:center;justify-content:center}

/* welcome */
.welcome{position:absolute;left:0;top:750px;width:1200px;height:290px;text-align:center;padding:0 200px}
.welcome h2{font-size:26px;line-height:1.35;color:var(--ink)}
.welcome p{margin:22px auto 28px;font-size:13px}

/* categories */
.categories{position:absolute;left:0;top:1048px;width:1200px;height:340px;background:var(--light)}
.cards{position:absolute;left:112px;top:60px;width:976px;display:flex;gap:40px}
.card{width:299px}
.card-photo{height:130px;border-radius:2px}
.card h3{font-size:18px;color:var(--blue);margin:16px 0 8px}
.card p{font-size:13px;line-height:1.55}

/* feature */
.feature{position:absolute;left:0;top:1410px;width:1200px;height:310px}
.video{position:absolute;left:112px;top:10px;width:490px;height:280px;background:linear-gradient(135deg,#2a1e14,#6b4726 50%,#1a120c)}
.video-bar{position:absolute;left:0;bottom:0;width:100%;height:30px;background:rgba(0,0,0,.7)}
.feature-copy{position:absolute;left:636px;top:10px;width:452px}
.feature-copy h2{font-size:28px;line-height:1.2}
.feature-copy h4{color:var(--blue);font-size:15px;margin:10px 0 14px;font-weight:600}
.feature-copy p{font-size:13px;margin-bottom:12px}

/* blog */
.blog{position:absolute;left:0;top:1760px;width:1200px;height:560px}
.blog-head{position:absolute;left:112px;top:0;width:976px;display:flex;justify-content:space-between;align-items:center}
.blog-head h2{font-size:30px}
.blog-nav{display:flex;gap:6px}
.blog-nav span{width:26px;height:26px;background:#d8d8d8;display:flex;align-items:center;justify-content:center}
.blog-box{position:absolute;left:112px;top:76px;width:850px;height:460px;background:var(--light)}
.blog-text{position:absolute;left:40px;top:40px;width:520px}
.blog-text h3{font-size:22px;margin-bottom:10px}
.meta{display:flex;gap:18px;font-size:12px;color:var(--muted);margin-bottom:18px}
.meta span::before{content:"";display:inline-block;width:8px;height:8px;background:var(--blue);margin-right:6px}
.blog-text p{font-size:13px;margin-bottom:12px}
.blog-photo{position:absolute;left:680px;top:116px;width:420px;height:300px;background:linear-gradient(135deg,#3a1a10,#8a3a1e 50%,#2a140c)}

/* footer */
.footer{position:absolute;left:0;top:2360px;width:1200px;height:360px;background:var(--dark);padding:48px 112px;display:flex;gap:50px}
.col{flex:1}
.col h4{font-size:17px;color:var(--white);margin-bottom:22px}
.col h4 em{font-style:normal;color:var(--blue)}
.col p{color:#9aa0a6;font-size:12px;line-height:1.6}
.post{margin-bottom:16px}
.post small{display:block;color:var(--blue);font-size:11px}
.ticks{list-style:none}
.ticks li{display:flex;gap:10px;align-items:center;color:#9aa0a6;font-size:12px;margin-bottom:12px}
.ticks li i{width:14px;height:14px;background:var(--blue);display:flex;align-items:center;justify-content:center;flex:none}
.contact p{margin-bottom:10px}
.contact b{color:var(--white);font-weight:600}
.subscribe{display:flex;margin:14px 0 10px}
.subscribe span{flex:1;height:34px;background:var(--white);font-size:12px;color:#999;padding:9px 10px}
.subscribe b{background:var(--blue);color:var(--white);font-size:12px;padding:9px 14px;font-weight:600}
.bottombar{position:absolute;left:0;top:2720px;width:1200px;height:64px;background:var(--darker);display:flex;flex-direction:column;align-items:center;justify-content:center;gap:8px}
.socials{display:flex;gap:10px}
.socials span{width:20px;height:20px;border-radius:50%;background:#3a3f45}
.bottombar small{color:#7a8086;font-size:11px}
</style>
</head>
<body>

<section class="hero">
  <div class="hero-photo" role="img" aria-label="Night view of a building forecourt lit by LED street lamps"></div>
  <header class="topbar">
    <div class="brand"><span class="brand-mark"></span>H&amp;V Business Solutions</div>
    <nav class="nav">
      <a class="active">Home</a><a>About Us</a><a>Products</a><a>Blog</a><a>Contact Us</a>
    </nav>
  </header>
  <div class="arrow" style="left:28px;top:380px"><svg width="14" height="14" viewBox="0 0 14 14"><path d="M9 2L4 7l5 5" stroke="#fff" stroke-width="2" fill="none"/></svg></div>
  <div class="arrow" style="right:28px;top:380px"><svg width="14" height="14" viewBox="0 0 14 14"><path d="M5 2l5 5-5 5" stroke="#fff" stroke-width="2" fill="none"/></svg></div>
  <div class="hero-copy">
    <h1 class="heading">LED Lights</h1>
    <h2 class="heading">Save businesses money on maintenance</h2>
    <p>Nemo enim ipsam voluptatem quia voluptas sit aspernatur aut odit aut fugit, sed quia consequuntur magni dolores eos qui ratione voluptatem sequi nesciunt.</p>
    <span class="btn btn-red">Get More &nbsp;
      <svg width="12" height="16" viewBox="0 0 12 16"><path d="M6 1a5 5 0 0 0-3 9v2h6v-2a5 5 0 0 0-3-9zM4 13h4v2H4z" fill="#fff"/></svg>
    </span>
  </div>
</section>

<section class="welcome">
  <h2 class="heading">Welcome to the commercial lighting division of<br>Harlow &amp; Venn Business Solutions</h2>
  <p>Harlow &amp; Venn lighting is a specialised commercial lighting partner supplying induction and LED fittings to car parks, schools, hotels, offices, shops and warehouses. Our range lowers energy use and cuts maintenance for your business, and our team helps you choose the right fittings and plan a switch that pays for itself over a short time.</p>
  <span class="btn btn-blue">Read More</span>
</section>

<section class="categories">
  <div class="arrow" style="left:20px;top:135px;background:#d6d8da"><svg width="14" height="14" viewBox="0 0 14 14"><path d="M9 2L4 7l5 5" stroke="#fff" stroke-width="2" fill="none"/></svg></div>
  <div class="arrow" style="right:20px;top:135px;background:#d6d8da"><svg width="14" height="14" viewBox="0 0 14 14"><path d="M5 2l5 5-5 5" stroke="#fff" stroke-width="2" fill="none"/></svg></div>
  <div class="cards">
    <article class="card">
      <div class="card-photo" role="img" aria-label="Underground car park with bright ceiling lighting" style="background:linear-gradient(135deg,#8a7a5a,#d9c79a 55%,#6b5e44)"></div>
      <h3 class="heading">Car Park Lighting</h3>
      <p>Lorem ipsum dolor sit amet, consectetur adipiscing elit, sed do eiusmod tempor incidunt ut labore et dolore magna aliqua. Ut enim ad minim veniam.</p>
    </article>
    <article class="card">
      <div class="card-photo" role="img" aria-label="Hotel lobby lit with warm pendant lights" style="background:linear-gradient(135deg,#6a3f1c,#c98a45 55%,#4a2a12)"></div>
      <h3 class="heading">Hospitality Lighting</h3>
      <p>Lorem ipsum dolor sit amet, consectetur adipiscing elit, sed do eiusmod tempor incidunt ut labore et dolore magna aliqua. Ut enim ad minim veniam.</p>
    </article>
    <article class="card">
      <div class="card-photo" role="img" aria-label="Open plan office with panel lighting" style="background:linear-gradient(135deg,#b9c3cc,#eef1f4 55%,#9aa6b0)"></div>
      <h3 class="heading">Office Lighting</h3>
      <p>Lorem ipsum dolor sit amet, consectetur adipiscing elit, sed do eiusmod tempor incidunt ut labore et dolore magna aliqua. Ut enim ad minim veniam.</p>
    </article>
  </div>
</section>

<section class="feature">
  <div class="video" role="img" aria-label="Video still of glowing filament light bulbs">
    <svg style="position:absolute;left:210px;top:105px" width="70" height="50" viewBox="0 0 70 50"><rect width="70" height="50" rx="8" fill="rgba(0,0,0,.65)"/><path d="M28 14l18 11-18 11z" fill="#fff"/></svg>
    <div class="video-bar"></div>
  </div>
  <div class="feature-copy">
    <h2 class="heading">LED lights which save businesses</h2>
    <h4>Commercial lighting company</h4>
    <p>Lighting upgrades reduce energy bills and lower replacement costs across car parks, schools and shops, with fittings rated for long service life in every setting.</p>
    <p>Induction and LED fittings run cooler, need less maintenance and keep their light output for years. Our advisers review your site, compare options and plan a staged upgrade to suit your budget and your timeline.</p>
    <span class="btn btn-blue">Read More</span>
  </div>
</section>

<section class="blog">
  <div class="blog-head">
    <h2 class="heading">Our Blog</h2>
    <div class="blog-nav">
      <span><svg width="10" height="10" viewBox="0 0 10 10"><path d="M7 1L3 5l4 4" stroke="#fff" stroke-width="2" fill="none"/></svg></span>
      <span><svg width="10" height="10" viewBox="0 0 10 10"><path d="M3 1l4 4-4 4" stroke="#fff" stroke-width="2" fill="none"/></svg></span>
    </div>
  </div>
  <div class="blog-box">
    <div class="blog-text">
      <h3 class="heading">Perspiciatis unde omnis iste natus error</h3>
      <div class="meta"><span>Admin</span><span>Lighting</span><span>June 12</span></div>
      <p>Sed ut perspiciatis unde omnis iste natus error sit voluptatem accusantium doloremque laudantium, totam rem aperiam eaque ipsa quae ab illo inventore veritatis.</p>
      <p>Nemo enim ipsam voluptatem quia voluptas sit aspernatur aut odit aut fugit, sed quia consequuntur magni dolores eos qui ratione voluptatem sequi nesciunt. Neque porro quisquam est qui dolorem ipsum quia dolor sit amet consectetur.</p>
      <p>At vero eos et accusamus et iusto odio dignissimos ducimus qui blanditiis praesentium voluptatum deleniti atque corrupti quos dolores.</p>
      <span class="btn btn-blue" style="margin-top:6px">Read More</span>
    </div>
  </div>
  <div class="blog-photo" role="img" aria-label="Hotel lounge lit with warm red lighting"></div>
</section>

<footer class="footer">
  <div class="col">
    <h4 class="heading">Recent <em>Posts</em></h4>
    <div class="post"><p>Sed rhoncus nulla lectus, vitae rutrum velit iaculis at. Curabitur vestibulum erat non mi.</p><small>June 12, 2015 · By Admin</small></div>
    <div class="post"><p>The tips and tricks of saving on lighting costs for busy warehouses and large shop floors.</p><small>May 28, 2015 · By Admin</small></div>
  </div>
  <div class="col">
    <h4 class="heading">Induction and <em>LED Lights</em></h4>
    <ul class="ticks">
      <li><i><svg width="10" height="10" viewBox="0 0 10 10"><path d="M1 5l3 3 5-6" stroke="#fff" stroke-width="2" fill="none"/></svg></i>There are many variations of passages of lorem.</li>
      <li><i><svg width="10" height="10" viewBox="0 0 10 10"><path d="M1 5l3 3 5-6" stroke="#fff" stroke-width="2" fill="none"/></svg></i>Passage of lorem ipsum as many are available.</li>
      <li><i><svg width="10" height="10" viewBox="0 0 10 10"><path d="M1 5l3 3 5-6" stroke="#fff" stroke-width="2" fill="none"/></svg></i>Classical literature, discovered the undoubtable.</li>
      <li><i><svg width="10" height="10" viewBox="0 0 10 10"><path d="M1 5l3 3 5-6" stroke="#fff" stroke-width="2" fill="none"/></svg></i>Embedded in the middle of text, if you use it.</li>
      <li><i><svg width="10" height="10" viewBox="0 0 10 10"><path d="M1 5l3 3 5-6" stroke="#fff" stroke-width="2" fill="none"/></svg></i>Therefore always free from repetition and humour.</li>
      <li><i><svg width="10" height="10" viewBox="0 0 10 10"><path d="M1 5l3 3 5-6" stroke="#fff" stroke-width="2" fill="none"/></svg></i>There are many variations of passages of lorem.</li>
    </ul>
  </div>
  <div class="col contact">
    <h4 class="heading">Contact <em>Info</em></h4>
    <p>418 Corbel Street, Alderbrook,<br>NSW 2148</p>
    <p><b>Tel</b> 02 5550 1847 &nbsp; <b>Fax</b> 02 5550 1848</p>
    <p>hello@harlowvenn.example</p>
    <div class="subscribe"><span>Enter Email...</span><b>Submit</b></div>
    <p>Lorem ipsum dolor sit amet, consectetur adipiscing elit.</p>
  </div>
</footer>
<div class="bottombar">
  <div class="socials"><span></span><span></span><span></span><span></span></div>
  <small>Copyright © 2015 Harlow &amp; Venn Business Solutions. All rights reserved.</small>
</div>

</body>
</html>
```